Corporate Design für die Vela Serena! GmbH
Zielgruppe
Die Vela Serena! GmbH begibt sich auf den Weg mit den Firmen, die sie gründet, kauft, entwickelt und verkauft. Wir sind eine Holding, beteiligen uns an Firmen oder gründen diese neu. 'Vela Serena!' ist der Pilgergruß auf dem Jakobsweg - diesen bin ich schon 5 Mal gegangen und die Metapher 'Gründen als Weg/Pilgerreise' finde ich sehr zutreffend. Ferner gibt es einen gelben Pfeil auf dem Jakobsweg, der einen immer verfolgt und einem den Weg weist. Das sind wir auch.
Aufgabenstellung
Es ist am Ende das Tages eine Holding, bei der sich Gründer und Firmen melden sollen, weil sie Beratung oder Kapital brauchen - daher ist Seriosität zwar unbedingt notwendig aber sie soll nicht abschrecken, elitär, 'Anwalt-grau-blau-weiß-bieder' sein. Gründertum, Unternehmertum, Freude, Machen, Erfolg!
Pilgern macht Freude und Gründen und Firmen haben auch. Mit uns um so mehr! Ein toller Weg!
'Vela Serena!' eben
Wir heißen 'Vela Serena! GmbH' - mit einem Ausrufezeichen angemeldet und das ist wichtig. Wir haben keine 'Fragezeichen' oder 'Punkte' wir haben ein Ausrufezeichen und einen Pfeil, ein Ziel, einen Weg, Etappen...
Die Abkürzung 'VS!' kann eine Möglichkeit sein aber ausgeschrieben wäre mir lieber - VS! kann das Favicon oder eine Logo-Kurzform/Variante sein

```html
<!DOCTYPE html>
<html lang="de">
<head>
<meta charset="utf-8">
<title>Vela Serena! GmbH – Corporate Design</title>
<link href="https://fonts.googleapis.com/css2?family=Mulish:wght@400;600;700&display=swap" rel="stylesheet">
<style>
  :root {
    --ink: #4a4a4a;
    --sun: #ffc600;
    --paper: #ffffff;
    --ghost: #ececec;
    --window: #cccccc;
    --shadow: 0 6px 18px rgba(0,0,0,.28);
  }
  * { box-sizing: border-box; margin: 0; padding: 0; }
  html, body { width: 1200px; height: 5108px; overflow: hidden; background: var(--paper); }
  body { position: relative; font-family: "Mulish", sans-serif; color: var(--ink); }

  /* wordmark */
  .logo { position: absolute; display: flex; flex-direction: column; align-items: flex-start; font-weight: 400; line-height: .95; color: var(--ink); letter-spacing: .01em; }
  .logo-square { width: .45em; height: .45em; background: var(--sun); margin-bottom: .18em; }
  .logo.on-dark { color: #fff; }
  .logo.ghost { color: var(--ghost); }
  .logo.ghost .logo-square { background: #f4f4f4; }

  .sheet { position: absolute; background: var(--paper); box-shadow: var(--shadow); overflow: hidden; }
  .band { position: absolute; background: var(--ink); }

  /* letterhead */
  .window-mark { position: absolute; width: 12px; height: 12px; border-color: #9a9a9a; border-style: solid; border-width: 0; }
  .sender { position: absolute; font-size: 12px; font-weight: 600; }
  .contacts { position: absolute; list-style: none; font-size: 15px; line-height: 22px; }
  .contacts li { display: flex; align-items: center; gap: 10px; }
  .contacts svg { width: 13px; height: 13px; fill: currentColor; flex: none; }
  .footer-col { position: absolute; font-size: 14px; line-height: 19px; padding-left: 10px; border-left: 2px solid var(--sun); }
  .fold { position: absolute; left: 0; width: 12px; height: 1px; background: #777; }

  /* cards */
  .person { position: absolute; font-size: 15px; line-height: 16px; }
  .person strong { font-weight: 700; display: block; }
  .person span { font-size: 12px; }
  .address { position: absolute; font-size: 12px; line-height: 14px; }
  .card .contacts { font-size: 12px; line-height: 18px; }
  .card .contacts svg { width: 11px; height: 11px; }
  .dark-panel { position: absolute; background: var(--ink); color: #fff; }

  .env-window { position: absolute; background: var(--window); border-radius: 22px; }
  .flap { position: absolute; left: 0; top: 0; width: 1030px; height: 146px; }
</style>
</head>
<body>

<!-- primary wordmark -->
<div class="logo" style="left:300px; top:210px; font-size:120px;">
  <div class="logo-square"></div><div>Vela</div><div>Serena!</div>
</div>

<!-- secondary wordmark -->
<div class="logo" style="left:300px; top:980px; font-size:120px;">
  <div class="logo-square"></div><div>Vela</div><div>Serena!</div>
</div>

<!-- letterhead -->
<section class="sheet letterhead" style="left:84px; top:1620px; width:1016px; height:1440px;">
  <div class="band" style="left:0; top:0; width:34px; height:1440px;"></div>
  <div class="fold" style="top:506px; left:0;"></div>
  <div class="fold" style="top:1014px; left:0;"></div>

  <div class="window-mark" style="left:106px; top:216px; border-top-width:1px; border-left-width:1px;"></div>
  <div class="window-mark" style="left:510px; top:216px; border-top-width:1px; border-right-width:1px;"></div>
  <div class="window-mark" style="left:106px; top:422px; border-bottom-width:1px; border-left-width:1px;"></div>
  <div class="window-mark" style="left:510px; top:422px; border-bottom-width:1px; border-right-width:1px;"></div>
  <p class="sender" style="left:122px; top:228px;">Vela Serena! GmbH | Musterstrasse 123 | 12345 Musterstadt</p>

  <div class="logo" style="left:736px; top:62px; font-size:46px;">
    <div class="logo-square"></div><div>Vela</div><div>Serena!</div>
  </div>

  <ul class="contacts" style="left:728px; top:264px;">
    <li><svg viewBox="0 0 16 16"><path d="M3 1l3 3-2 2c1 2 3 4 5 5l2-2 3 3-2 3C6 15 1 10 1 3z"/></svg>+41 123 / 45 67 89 01</li>
    <li><svg viewBox="0 0 16 16"><path d="M4 1h7v4H4zM1 6h14v6h-3v3H4v-3H1zM5 10v3h6v-3z"/></svg>+41 123 / 45 67 89 01</li>
    <li><svg viewBox="0 0 16 16"><path d="M1 3h14v10H1zM2 4l6 5 6-5v1L8 10 2 5z"/></svg>info@vela-serena.de</li>
    <li><svg viewBox="0 0 16 16"><path d="M8 1a7 7 0 100 14A7 7 0 008 1zm0 1.5c.8 1 1.3 2.5 1.5 4.5h-3C6.7 5 7.2 3.5 8 2.5zM2.6 7h2.4c.1-1.7.4-3 1-4A5.5 5.5 0 002.6 7zm0 2A5.5 5.5 0 006 13c-.6-1-.9-2.3-1-4zm4 0h3c-.2 2-.7 3.5-1.5 4.5-.8-1-1.3-2.5-1.5-4.5zm4.4 0c-.1 1.7-.4 3-1 4a5.5 5.5 0 003.4-4zm2.4-2A5.5 5.5 0 0010 3c.6 1 .9 2.3 1 4z"/></svg>www.vela-serena.de</li>
  </ul>

  <div class="logo ghost" style="left:300px; top:650px; font-size:92px;">
    <div class="logo-square"></div><div>Vela</div><div>Serena!</div>
  </div>

  <div class="footer-col" style="left:96px; top:1366px;">Musterstrasse 123<br>12345 Musterstadt<br>Geschäftsführung Max Muster</div>
  <div class="footer-col" style="left:386px; top:1366px;">Bankverbindung<br>BIC:&nbsp; ABCDEFGHXXX<br>IBAN: DE 00 0000 0000 0000 0000 00</div>
  <div class="footer-col" style="left:764px; top:1366px;">Finanzamt<br>Musterstadt<br>USt-IdNr.: DE000000000</div>
</section>

<!-- business card 1: front dark -->
<section class="sheet card" style="left:96px; top:3144px; width:484px; height:314px; background:var(--ink);">
  <div class="logo on-dark" style="left:150px; top:66px; font-size:58px;">
    <div class="logo-square"></div><div>Vela</div><div>Serena!</div>
  </div>
</section>

<!-- business card 2: back with dark panel -->
<section class="sheet card" style="left:630px; top:3144px; width:484px; height:314px;">
  <div class="person" style="left:12px; top:166px;"><strong>MAX MUSTER</strong><span>Patentanwalt</span></div>
  <div class="address" style="left:12px; top:272px;">Musterstrasse 123<br>12345 Musterstadt</div>
  <div class="dark-panel" style="left:240px; top:0; width:244px; height:314px;">
    <div class="logo on-dark" style="left:46px; top:24px; font-size:36px;">
      <div class="logo-square"></div><div>Vela</div><div>Serena!</div>
    </div>
    <ul class="contacts" style="left:16px; top:208px;">
      <li><svg viewBox="0 0 16 16"><path d="M3 1l3 3-2 2c1 2 3 4 5 5l2-2 3 3-2 3C6 15 1 10 1 3z"/></svg>+41 123 / 45 67 89 01</li>
      <li><svg viewBox="0 0 16 16"><path d="M4 1h7v4H4zM1 6h14v6h-3v3H4v-3H1zM5 10v3h6v-3z"/></svg>+41 123 / 45 67 89 01</li>
      <li><svg viewBox="0 0 16 16"><path d="M4 1h8v14H4zm1 2v9h6V3z"/></svg>+41 123 / 45 67 89 01</li>
      <li><svg viewBox="0 0 16 16"><path d="M1 3h14v10H1zM2 4l6 5 6-5v1L8 10 2 5z"/></svg>info@vela-serena.de</li>
      <li><svg viewBox="0 0 16 16"><circle cx="8" cy="8" r="7"/></svg>www.vela-serena.de</li>
    </ul>
  </div>
</section>

<!-- business card 3: front white -->
<section class="sheet card" style="left:96px; top:3532px; width:484px; height:314px;">
  <div class="band" style="left:0; top:0; width:28px; height:314px;"></div>
  <div class="logo" style="left:164px; top:66px; font-size:58px;">
    <div class="logo-square"></div><div>Vela</div><div>Serena!</div>
  </div>
</section>

<!-- business card 4: back white -->
<section class="sheet card" style="left:630px; top:3532px; width:484px; height:314px;">
  <div class="band" style="left:0; top:0; width:26px; height:314px;"></div>
  <div class="person" style="left:44px; top:166px;"><strong>MAX MUSTER</strong><span>Patentanwalt</span></div>
  <div class="address" style="left:44px; top:272px;">Musterstrasse 123<br>12345 Musterstadt</div>
  <div class="logo" style="left:302px; top:22px; font-size:36px;">
    <div class="logo-square"></div><div>Vela</div><div>Serena!</div>
  </div>
  <ul class="contacts" style="left:300px; top:208px;">
    <li><svg viewBox="0 0 16 16"><path d="M3 1l3 3-2 2c1 2 3 4 5 5l2-2 3 3-2 3C6 15 1 10 1 3z"/></svg>+41 123 / 45 67 89 01</li>
    <li><svg viewBox="0 0 16 16"><path d="M4 1h7v4H4zM1 6h14v6h-3v3H4v-3H1zM5 10v3h6v-3z"/></svg>+41 123 / 45 67 89 01</li>
    <li><svg viewBox="0 0 16 16"><path d="M4 1h8v14H4zm1 2v9h6V3z"/></svg>+41 123 / 45 67 89 01</li>
    <li><svg viewBox="0 0 16 16"><path d="M1 3h14v10H1zM2 4l6 5 6-5v1L8 10 2 5z"/></svg>info@vela-serena.de</li>
    <li><svg viewBox="0 0 16 16"><circle cx="8" cy="8" r="7"/></svg>www.vela-serena.de</li>
  </ul>
</section>

<!-- envelope front -->
<section class="sheet envelope" style="left:90px; top:3962px; width:1030px; height:514px;">
  <div class="band" style="left:0; top:0; width:1030px; height:12px;"></div>
  <div class="band" style="left:0; top:502px; width:1030px; height:12px;"></div>
  <div class="logo" style="left:228px; top:80px; font-size:38px;">
    <div class="logo-square"></div><div>Vela</div><div>Serena!</div>
  </div>
  <div class="env-window" style="left:90px; top:246px; width:402px; height:198px;"></div>
</section>

<!-- envelope back -->
<section class="sheet envelope" style="left:90px; top:4546px; width:1030px; height:514px;">
  <svg class="flap" viewBox="0 0 1030 146" aria-hidden="true">
    <path d="M0 0H1030L990 126Q984 146 960 146H70Q46 146 40 126Z" fill="#4a4a4a"/>
  </svg>
  <div class="logo on-dark" style="left:466px; top:22px; font-size:34px;">
    <div class="logo-square"></div><div>Vela</div><div>Serena!</div>
  </div>
  <div class="band" style="left:0; top:502px; width:1030px; height:12px;"></div>
</section>

</body>
</html>
```